Sparrow Haulage needs a business card design.

Design a double-sided business card for new freight business. On the front, would like to see our logo along with the following info:

Martin Obuya
CEO/FOUNDER
555-206-7142
martinobuya@sparrow-haulage.example

On the reverse side, we would like to use the graphic image of our logo only without the Sparrow Haulage name.

```html
<!DOCTYPE html>
<html lang="en">
<head>
<meta charset="utf-8">
<title>Sparrow Haulage – Business Card</title>
<link rel="stylesheet" href="https://fonts.googleapis.com/css2?family=Montserrat:wght@600&family=Open+Sans:wght@400&display=swap">
<style>
  :root {
    --stage: #1d1d20;
    --navy: #1b1a5c;
    --navy-light: #2a2a7a;
    --red: #b81f2a;
    --white: #ffffff;
    --muted: #d9d9ee;
  }
  * { box-sizing: border-box; margin: 0; padding: 0; }
  html, body { width: 1200px; height: 948px; overflow: hidden; }
  body {
    background: var(--stage);
    display: flex;
    align-items: center;
    justify-content: center;
    gap: 40px;
    font-family: "Open Sans", sans-serif;
  }
  .card {
    position: relative;
    width: 540px;
    height: 320px;
    border-radius: 22px;
    overflow: hidden;
    background: var(--navy);
    box-shadow: 0 18px 40px rgba(0,0,0,.45);
  }
  /* Back side: pattern field with the brand symbol position only */
  .card-back .pattern-fill {
    position: absolute;
    inset: 0;
    background: radial-gradient(circle at 35% 30%, var(--navy-light), var(--navy) 70%);
  }
  .card-back .symbol-spot {
    position: absolute;
    right: 120px;
    top: 140px;
    width: 22px;
    height: 22px;
    background: var(--white);
  }
  /* Front side */
  .card-front .curve-panel {
    position: absolute;
    inset: 0;
  }
  .card-front .brand-mark {
    position: absolute;
    left: 310px;
    top: 70px;
    display: flex;
    align-items: center;
    gap: 12px;
    font-family: "Montserrat", sans-serif;
    font-weight: 600;
    font-size: 22px;
    line-height: 1.05;
    letter-spacing: 2px;
    color: var(--navy);
    text-transform: uppercase;
  }
  .brand-square {
    width: 16px;
    height: 16px;
    background: currentColor;
    flex: none;
  }
  .holder {
    position: absolute;
    left: 38px;
    top: 150px;
    color: var(--white);
  }
  .holder-name {
    font-family: "Montserrat", sans-serif;
    font-weight: 600;
    font-size: 21px;
    letter-spacing: 1.5px;
    text-transform: uppercase;
  }
  .holder-title {
    margin-top: 4px;
    font-size: 13px;
    letter-spacing: 1px;
    color: var(--muted);
  }
  .contact-list {
    position: absolute;
    left: 38px;
    bottom: 30px;
    list-style: none;
    color: var(--white);
    font-size: 12.5px;
    line-height: 1.75;
  }
  .contact-list li { display: flex; align-items: center; gap: 9px; }
  .contact-list svg { width: 12px; height: 12px; fill: var(--white); flex: none; }
</style>
</head>
<body>

  <section class="card card-back" aria-label="Business card back">
    <div class="pattern-fill" role="img" aria-label="Repeating tonal pattern of the brand symbol on navy"></div>
    <span class="symbol-spot" role="img" aria-label="Brand symbol"></span>
  </section>

  <section class="card card-front" aria-label="Business card front">
    <svg class="curve-panel" viewBox="0 0 540 320" aria-hidden="true">
      <circle cx="500" cy="-8" r="300" fill="var(--red)"/>
      <circle cx="512" cy="-22" r="300" fill="var(--white)"/>
    </svg>

    <div class="brand-mark"><span class="brand-square"></span><span>Sparrow<br>Haulage</span></div>

    <div class="holder">
      <h1 class="holder-name">Martin Obuya</h1>
      <p class="holder-title">CEO/FOUNDER</p>
    </div>

    <ul class="contact-list">
      <li>
        <svg viewBox="0 0 24 24"><path d="M6.6 10.8a15.1 15.1 0 0 0 6.6 6.6l2.2-2.2a1 1 0 0 1 1-.25 11.4 11.4 0 0 0 3.6.57 1 1 0 0 1 1 1V20a1 1 0 0 1-1 1A17 17 0 0 1 3 4a1 1 0 0 1 1-1h3.5a1 1 0 0 1 1 1c0 1.25.2 2.45.57 3.57a1 1 0 0 1-.25 1z"/></svg>
        555-206-7142
      </li>
      <li>
        <svg viewBox="0 0 24 24"><path d="M2 5h20v14H2zm2 2v.5l8 5 8-5V7zm0 2.9V17h16V9.9l-8 5z"/></svg>
        martinobuya@sparrow-haulage.example
      </li>
      <li>
        <svg viewBox="0 0 24 24"><path d="M12 2a10 10 0 1 0 0 20 10 10 0 0 0 0-20zm6.9 6h-3a15 15 0 0 0-1.3-3.9A8 8 0 0 1 18.9 8zM12 4a13 13 0 0 1 1.9 4h-3.8A13 13 0 0 1 12 4zM4.3 14a8 8 0 0 1 0-4h3.4a16 16 0 0 0 0 4zm.8 2h3a15 15 0 0 0 1.3 3.9A8 8 0 0 1 5.1 16zm3-8h-3a8 8 0 0 1 4.3-3.9A15 15 0 0 0 8.1 8zM12 20a13 13 0 0 1-1.9-4h3.8A13 13 0 0 1 12 20zm2.3-6H9.7a14 14 0 0 1 0-4h4.6a14 14 0 0 1 0 4zm.3 5.9a15 15 0 0 0 1.3-3.9h3a8 8 0 0 1-4.3 3.9zm1.7-5.9a16 16 0 0 0 0-4h3.4a8 8 0 0 1 0 4z"/></svg>
        www.sparrow-haulage.example
      </li>
    </ul>
  </section>

</body>
</html>
```